WTF!!! We need a modern professional website for a business litigation law firm.

We need a modern, clean, professional and uncomplicated website for a new business trial and litigation law firm called "Haverlock Trial Firm PLLC". Website must be mobile optimized for iPad and smartphone. The law firm specializes in counseling and representing large corporations, small businesses and entrepreneurs in and out of the courtroom. Lawyers in the firm serve as Florida counsel and trial counsel to organizations facing claims involving product liability, premises liability, professional liability, vehicle and transportation liability, warranty claims, construction defects and delay claims, complex business disputes, commercial litigation and bid disputes in State and Federal Courts. The website is mainly to provide information about the firm, and should include sections describing the firm, identifying the Industries Served and Areas of Practice ," a separate page identifying the "Professionals", a separate page for "Resources & Advisories," and a traveling "Connect With Us" button a site visitor can click on that will launch an email to the Firm's general email account. The website should allow us to easily modify the content on these pages, and let us add/modify links to external information sources. We will not sell anything or take payments through the website. We do need to be able to easily upload and update photographs of attorneys and add new attorneys names/email hyperlinks as the firm grows. We would like to add developments in the law or success stories easily and quickly, such as through a blog page. On the "Connect With Us" page the website should have hyperlinks to email the Firm, and there should be hyperlinks to email each professional on the "Professionals" page. The website should be viewable on mobile devices without distortion. The law firm focuses on trial work and should have some imagery associated with courtrooms, but the overall theme of the site should be modern, clean, and communicate sophistication and strength. The website should be made in Wordpress. We have uploaded logo files for Haverlock Trial Firm.

Target Market(s)

Corporations and companies that are looking for legal representation. Other attorneys/legal industry.

Industry/Entity Type

Legal Industry

Coding

Coded - Design and coding required

Number of Pages Required

1 page

Font styles to use
Sans Serif

Requirements
Must have
• Simple, clean, sophisticated, modern website that includes the logo, watermark of logo, and the elements described above.
Nice to have
• Pictures of city scape, buildings, courtroom, team members.

```html
<!DOCTYPE html>
<html lang="en">
<head>
<meta charset="utf-8">
<title>Haverlock Trial Firm</title>
<link href="https://fonts.googleapis.com/css2?family=Poppins:wght@400;500;600;700;800&family=Roboto:wght@400;500&family=Lora:ital@1&family=Merriweather:wght@700&display=swap" rel="stylesheet">
<style>
:root{
  --orange:#f4511e;
  --orange-dark:#d9400f;
  --ink:#111111;
  --text:#555555;
  --grey-bg:#f2f2f2;
  --white:#ffffff;
  --night:#1d2738;
}
*{box-sizing:border-box;margin:0;padding:0}
html,body{width:1200px;height:3376px;overflow:hidden;background:var(--white)}
body{position:relative;font-family:'Roboto',sans-serif;color:var(--text)}
.abs{position:absolute}

/* Header */
.site-header{position:absolute;left:0;top:0;width:1200px;height:120px;background:var(--white)}
.brand{position:absolute;left:22px;top:22px;display:flex;align-items:center;gap:10px}
.brand-mark{width:22px;height:22px;background:var(--orange)}
.brand-name{font-family:'Poppins',sans-serif;font-weight:700;font-size:20px;color:var(--ink);line-height:1.1;width:130px}
.contact-bar{position:absolute;left:380px;top:0;width:820px;height:56px;background:var(--orange);
  clip-path:polygon(40px 0,100% 0,100% 100%,0 100%)}
.contact-bar .item{position:absolute;top:18px;color:var(--white);font-family:'Poppins',sans-serif;font-size:14px;font-weight:500;display:flex;align-items:center;gap:8px}
.main-nav{position:absolute;left:356px;top:62px;display:flex;gap:26px;font-family:'Poppins',sans-serif;font-size:13px;font-weight:500;color:var(--ink)}
.main-nav a{color:inherit;text-decoration:none;padding-bottom:6px}
.main-nav a.active{color:var(--orange);border-bottom:2px solid var(--orange)}

/* Hero */
.hero{position:absolute;left:0;top:120px;width:1200px;height:580px;overflow:hidden}
.hero-photo{position:absolute;inset:0;background:linear-gradient(180deg,#6f7e93 0%,#3a4a63 45%,#1f2a3d 75%,#2c3446 100%)}
.hero-title{position:absolute;left:0;top:170px;width:1200px;text-align:center;font-family:'Poppins',sans-serif;font-weight:800;font-size:46px;color:var(--white);letter-spacing:1px}
.hero-sub{position:absolute;left:300px;top:240px;width:600px;text-align:center;color:var(--white);font-size:17px;line-height:1.45}
.btn{display:inline-block;background:var(--orange);color:var(--white);font-family:'Poppins',sans-serif;font-weight:600;font-size:14px;text-decoration:none}
.hero .btn{position:absolute;left:502px;top:320px;width:196px;height:50px;line-height:50px;text-align:center}
.slide-arrow{position:absolute;width:50px;height:50px;border-radius:50%;border:2px solid var(--white);display:flex;align-items:center;justify-content:center}
.hero-cut{position:absolute;left:0;bottom:0}

/* Section heading */
.sec-title{font-family:'Poppins',sans-serif;font-weight:700;color:var(--ink);font-size:30px}
.para{font-size:15px;line-height:1.75;color:var(--text)}

/* Industries */
.industries-frame{position:absolute;left:120px;top:842px;width:440px;height:380px;border:3px solid var(--orange)}
.industries-photo{position:absolute;left:132px;top:826px;width:430px;height:372px;background:linear-gradient(135deg,#c9b8a6,#8a7563 55%,#4c4038)}
.industries-body{position:absolute;left:632px;top:828px;width:540px}
.industries-body .sec-title{position:relative;padding-left:0}
.industries-body .rule{position:absolute;left:632px;top:808px}
.industries-body .para{margin-top:22px}
.industries-body .btn{margin-top:24px;padding:0 30px;height:50px;line-height:50px}

/* Areas */
.areas{position:absolute;left:0;top:1340px;width:1200px;height:500px;background:var(--orange)}
.areas-intro{position:absolute;left:112px;top:72px;width:250px;color:var(--white)}
.areas-intro h2{font-family:'Poppins',sans-serif;font-weight:700;font-size:30px;line-height:1.3}
.areas-intro h2 span{display:inline-block;width:60px;height:3px;background:var(--white);vertical-align:middle;margin-left:8px}
.areas-intro p{margin-top:20px;font-size:15px;line-height:1.6;color:var(--white)}
.pager{position:absolute;left:112px;top:352px;display:flex}
.pager div{width:56px;height:56px;display:flex;align-items:center;justify-content:center}
.practice-card{position:absolute;top:80px;width:216px;height:330px;background:#fff4ef;padding:28px 22px}
.practice-card h3{margin-top:18px;font-family:'Poppins',sans-serif;font-weight:700;font-size:16px;color:var(--orange);line-height:1.35}
.practice-card p{margin-top:14px;font-size:14px;line-height:1.55;color:var(--text)}
.practice-card .view{position:absolute;left:22px;bottom:26px;font-family:'Poppins',sans-serif;font-size:14px;font-weight:600;color:var(--ink);display:flex;align-items:center;gap:8px}

/* Stories */
.stories-title{position:absolute;left:0;top:1944px;width:1200px;text-align:center}
.stories-title .rule{display:inline-block;width:100px;height:3px;background:var(--orange);vertical-align:middle;margin:0 18px}
.quote{position:absolute;left:210px;top:2010px;width:780px;text-align:center;font-family:'Lora',serif;font-style:italic;font-size:22px;line-height:1.55;color:#444}
.quote-mark{position:absolute;left:212px;top:2008px;font-family:'Lora',serif;font-size:48px;color:#999;line-height:1}
.client{position:absolute;left:0;top:2160px;width:1200px;text-align:center;font-family:'Poppins',sans-serif;font-weight:700;font-size:17px;color:var(--ink)}
.stars{position:absolute;left:0;top:2190px;width:1200px;text-align:center;color:#f5a623;font-size:16px;letter-spacing:2px}

/* Blog */
.blog{position:absolute;left:0;top:2300px;width:1200px;height:660px;background:var(--grey-bg)}
.blog .sec-title{position:absolute;left:0;top:86px;width:1200px;text-align:center;font-size:34px}
.blog .underline{position:absolute;left:560px;top:142px;width:80px;height:3px;background:var(--ink)}
.post{position:absolute;top:204px;width:296px;height:404px;background:var(--white)}
.post.featured{box-shadow:0 6px 22px rgba(0,0,0,.18)}
.post .thumb{width:100%;height:178px}
.post h4{margin:28px 22px 0;font-family:'Merriweather',serif;font-weight:700;font-size:16px;line-height:1.5;color:var(--ink)}
.post.featured h4{color:var(--orange)}
.post p{margin:14px 22px 0;font-size:14px;line-height:1.55;color:var(--text)}
.post .more{position:absolute;left:22px;bottom:28px;display:flex;align-items:center;gap:10px;font-family:'Poppins',sans-serif;font-size:14px;font-weight:500;color:var(--orange)}

/* Footer */
.site-footer{position:absolute;left:0;top:2960px;width:1200px;height:416px;background:#050505;color:var(--white)}
.footer-brand{position:absolute;left:150px;top:96px;display:flex;align-items:center;gap:14px}
.footer-brand .brand-mark{width:30px;height:30px}
.footer-brand .brand-name{color:var(--white);font-size:30px;width:210px;line-height:1.15}
.f-col{position:absolute;top:60px;display:flex;gap:20px}
.f-col .lbl{font-family:'Poppins',sans-serif;font-size:16px;font-weight:500;text-transform:uppercase}
.f-col .val{font-size:15px;line-height:1.5;color:#ddd}
.f-col .blk{margin-bottom:18px}
.socials{position:absolute;left:560px;top:172px;display:flex;gap:16px}
.socials span{width:34px;height:34px;border-radius:50%;border:2px solid var(--white)}
.footer-rule{position:absolute;left:0;top:340px;width:1200px;height:1px;background:#333}
.copyright{position:absolute;left:0;top:366px;width:1200px;text-align:center;font-size:14px;color:#ddd}
</style>
</head>
<body>

<header class="site-header">
  <div class="brand"><span class="brand-mark"></span><span class="brand-name">Haverlock Trial Firm</span></div>
  <div class="contact-bar">
    <div class="item" style="left:170px">
      <svg width="16" height="16" viewBox="0 0 24 24" fill="#fff"><path d="M6.6 10.8a15.1 15.1 0 0 0 6.6 6.6l2.2-2.2a1 1 0 0 1 1-.25 11.4 11.4 0 0 0 3.6.57 1 1 0 0 1 1 1V20a1 1 0 0 1-1 1A17 17 0 0 1 3 4a1 1 0 0 1 1-1h3.5a1 1 0 0 1 1 1c0 1.25.2 2.45.57 3.57a1 1 0 0 1-.25 1z"/></svg>
      PHONE: +1 888 555 0147
    </div>
    <div class="item" style="left:470px">
      <svg width="16" height="16" viewBox="0 0 24 24" fill="#fff"><path d="M2 5h20v14H2z" fill="none" stroke="#fff" stroke-width="2"/><path d="M2 5l10 8 10-8" fill="none" stroke="#fff" stroke-width="2"/></svg>
      EMAIL: info@haverlocktrialfirm.com
    </div>
  </div>
  <nav class="main-nav">
    <a class="active" href="#">HOME</a>
    <a href="#">INDUSTRIES SERVED</a>
    <a href="#">AREAS OF PRACTICE</a>
    <a href="#">PROFESSIONALS</a>
    <a href="#">RESOURCES &amp; ADVISORIES</a>
  </nav>
</header>

<section class="hero">
  <div class="hero-photo" role="img" aria-label="City skyline of office towers along the waterfront at dusk"></div>
  <h1 class="hero-title">HAVERLOCK TRIAL FIRM</h1>
  <p class="hero-sub">Lorem ipsum dolor sit amet, consectetur adipiscing elit, sed do eiusmod tempor incididunt ut labore et dolore magna aliqua.</p>
  <a class="btn" href="#">CONNECT WITH US</a>
  <div class="slide-arrow" style="left:22px;top:255px"><svg width="18" height="18" viewBox="0 0 24 24"><path d="M15 5l-7 7 7 7" stroke="#fff" stroke-width="3" fill="none"/></svg></div>
  <div class="slide-arrow" style="left:1128px;top:255px"><svg width="18" height="18" viewBox="0 0 24 24"><path d="M9 5l7 7-7 7" stroke="#fff" stroke-width="3" fill="none"/></svg></div>
  <svg class="hero-cut" width="1200" height="120" viewBox="0 0 1200 120">
    <polygon points="0,82 1200,8 1200,34 0,108" fill="#f4511e"/>
    <polygon points="0,108 1200,34 1200,120 0,120" fill="#fff"/>
  </svg>
</section>

<div class="industries-frame"></div>
<div class="industries-photo" role="img" aria-label="Attorney meeting with a family in a bright office"></div>
<section class="industries-body">
  <h2 class="sec-title">INDUSTRIES WE SERVED</h2>
  <p class="para">Lorem ipsum dolor sit amet, consectetur adipiscing elit, sed do eiusmod tempor incididunt ut labore et dolore magna aliqua. Ut enim ad minim veniam, quis nostrud exercitation ullamco laboris nisi ut aliquip ex ea commodo consequat. Duis aute irure dolor in reprehenderit in voluptate velit esse cillum dolore eu fugiat nulla pariatur. Ut enim ad minima veniam, quis nostrum exercitationem ullam corporis Excepteur sint occaecat cupidatat non proident, sunt in culpa qui officia deserunt mollit anim id est laborum.</p>
  <a class="btn" href="#">READ MORE</a>
</section>
<div class="abs" style="left:632px;top:812px;width:40px;height:3px;background:#111"></div>

<section class="areas">
  <div class="areas-intro">
    <h2>AREAS OF<br>PRACTICE<span></span></h2>
    <p>Lorem ipsum dolor sit amet, consectetur adipiscing elit, sed do eiusmod tempor incididunt ut labore et dolore magna aliqua. Ut enim ad minim veniam, quis nostrud exercitation ullamco.</p>
  </div>
  <div class="pager">
    <div style="background:#fff"><svg width="18" height="18" viewBox="0 0 24 24"><path d="M20 12H5m6-6l-6 6 6 6" stroke="#111" stroke-width="2.5" fill="none"/></svg></div>
    <div style="background:#111"><svg width="18" height="18" viewBox="0 0 24 24"><path d="M4 12h15m-6-6l6 6-6 6" stroke="#fff" stroke-width="2.5" fill="none"/></svg></div>
  </div>

  <article class="practice-card" style="left:420px">
    <svg width="46" height="46" viewBox="0 0 48 48" fill="none" stroke="#333" stroke-width="2"><rect x="6" y="14" width="24" height="18" rx="2"/><path d="M30 20h7l5 6v6H30"/><circle cx="14" cy="35" r="4"/><circle cx="36" cy="35" r="4"/></svg>
    <h3>TRANSPORTATION LIABILITY</h3>
    <p>Ed quia non num-uam eius modi tem porarte dolore mag ntm.</p>
    <div class="view">VIEW <svg width="18" height="12" viewBox="0 0 18 12"><path d="M0 6h16m-5-5l5 5-5 5" stroke="#111" stroke-width="2" fill="none"/></svg></div>
  </article>
  <article class="practice-card" style="left:660px">
    <svg width="46" height="46" viewBox="0 0 48 48" fill="none" stroke="#333" stroke-width="2"><rect x="10" y="6" width="28" height="36" rx="2"/><path d="M16 16h16M16 23h16M16 30h10"/></svg>
    <h3>WARRANTY CLAIMS</h3>
    <p>Ed quia non num-uam eius modi tem porarte dolore mag ntm.</p>
    <div class="view">VIEW <svg width="18" height="12" viewBox="0 0 18 12"><path d="M0 6h16m-5-5l5 5-5 5" stroke="#111" stroke-width="2" fill="none"/></svg></div>
  </article>
  <article class="practice-card" style="left:900px">
    <svg width="46" height="46" viewBox="0 0 48 48" fill="none" stroke="#333" stroke-width="2"><circle cx="24" cy="16" r="9"/><path d="M24 11v10M21 13h5a2 2 0 0 1 0 4h-4a2 2 0 0 0 0 4h5"/><path d="M6 38c6-6 12-6 18-2s12 2 18-4"/></svg>
    <h3>COMMERCIAL LITIGATION</h3>
    <p>Ed quia non num-uam eius modi tem porarte dolore mag ntm.</p>
    <div class="view">VIEW <svg width="18" height="12" viewBox="0 0 18 12"><path d="M0 6h16m-5-5l5 5-5 5" stroke="#111" stroke-width="2" fill="none"/></svg></div>
  </article>
</section>

<section>
  <h2 class="sec-title stories-title"><span class="rule"></span>SUCCESS STORIES<span class="rule"></span></h2>
  <div class="quote-mark">&ldquo;</div>
  <p class="quote">Duis aute irure dolor in reprehenderit in voluptate velit esse cillum dolore eu fugiat nulla pariatur. Excepteur sint occaecat cupidatat non proident.</p>
  <div class="client">SAM CARTER</div>
  <div class="stars">★★★★★</div>
  <div class="slide-arrow" style="left:26px;top:2030px;border-color:#888"><svg width="16" height="16" viewBox="0 0 24 24"><path d="M15 5l-7 7 7 7" stroke="#888" stroke-width="3" fill="none"/></svg></div>
  <div class="slide-arrow" style="left:1116px;top:2030px;border-color:#111"><svg width="16" height="16" viewBox="0 0 24 24"><path d="M9 5l7 7-7 7" stroke="#111" stroke-width="3" fill="none"/></svg></div>
</section>

<section class="blog">
  <h2 class="sec-title">LATEST BLOG</h2>
  <div class="underline"></div>
  <article class="post" style="left:112px">
    <div class="thumb" role="img" aria-label="Colleagues reviewing documents around a table" style="background:linear-gradient(135deg,#d8c7ae,#8f7a62)"></div>
    <h4>Lorem ipsum dolor sit amet, consectetur adipiscing.</h4>
    <p>Lorem ipsum dolor sit amet, must consectetur adipiscing. Lorem dol ipsum dolor sit amet.</p>
    <div class="more"><svg width="18" height="12" viewBox="0 0 18 12"><path d="M0 6h16m-5-5l5 5-5 5" stroke="#111" stroke-width="2" fill="none"/></svg></div>
  </article>
  <article class="post" style="left:452px">
    <div class="thumb" role="img" aria-label="Team seated in a circle during a meeting" style="background:linear-gradient(135deg,#b7c0cc,#56647a)"></div>
    <h4>Lorem ipsum dolor sit amet, consectetur adipiscing.</h4>
    <p>Lorem ipsum dolor sit amet, must consectetur adipiscing. Lorem dol ipsum dolor sit amet.</p>
    <div class="more"><svg width="18" height="12" viewBox="0 0 18 12"><path d="M0 6h16m-5-5l5 5-5 5" stroke="#111" stroke-width="2" fill="none"/></svg></div>
  </article>
  <article class="post featured" style="left:792px">
    <div class="thumb" role="img" aria-label="Two professionals in discussion at a desk" style="background:linear-gradient(135deg,#c4c9cf,#6c737c)"></div>
    <h4>Lorem ipsum dolor sit amet, consectetur adipiscing.</h4>
    <p>Lorem ipsum dolor sit amet, must consectetur adipiscing. Lorem dol ipsum dolor sit amet.</p>
    <div class="more">Read More <svg width="18" height="12" viewBox="0 0 18 12"><path d="M0 6h16m-5-5l5 5-5 5" stroke="#f4511e" stroke-width="2" fill="none"/></svg></div>
  </article>
</section>

<footer class="site-footer">
  <div class="footer-brand"><span class="brand-mark"></span><span class="brand-name">Haverlock Trial Firm</span></div>
  <div class="f-col" style="left:560px">
    <svg width="22" height="22" viewBox="0 0 24 24" fill="none" stroke="#fff" stroke-width="2"><path d="M12 22s7-7 7-12a7 7 0 0 0-14 0c0 5 7 12 7 12z"/><circle cx="12" cy="10" r="2.5"/></svg>
    <div><div class="lbl">Address</div><div class="val">45 Harbor Point Road #210<br>UNITED STATES, 33601</div></div>
  </div>
  <div class="f-col" style="left:900px">
    <svg width="22" height="22" viewBox="0 0 24 24" fill="#fff"><path d="M6.6 10.8a15.1 15.1 0 0 0 6.6 6.6l2.2-2.2a1 1 0 0 1 1-.25 11.4 11.4 0 0 0 3.6.57 1 1 0 0 1 1 1V20a1 1 0 0 1-1 1A17 17 0 0 1 3 4a1 1 0 0 1 1-1h3.5a1 1 0 0 1 1 1c0 1.25.2 2.45.57 3.57a1 1 0 0 1-.25 1z"/></svg>
    <div>
      <div class="blk"><div class="lbl">Phone</div><div class="val">0345 210 7788</div></div>
      <div class="blk"><div class="lbl">Toll Free Fax</div><div class="val">+1 888 555 0192</div></div>
    </div>
  </div>
  <div class="socials"><span></span><span></span><span></span></div>
  <div class="footer-rule"></div>
  <div class="copyright">©2025 Haverlock Trial Firm PLLC All Rights Reserved</div>
</footer>

</body>
</html>
```